Small Business Broker Business Card Design

A business card design for a small business brokerage, which is a financial service, not unlike real estate brokerage, but for small businesses such as laundromats, pizza shops, restaurants, cleaners etc. The designs should all be simple, more conservative in nature, using the colors and font of the logo. Again, think real estate Brokerage as a business context
Contact Information for Business Card
Name: Glen R. Harlow. Title: Small Business Advisor. Email: g.harlow@bayfieldcapitalworks.example. Mobile: (555) 274-3918. Office: (555) 806-2147. www.bayfieldcapitalworks.example

```html
<!DOCTYPE html>
<html lang="en">
<head>
<meta charset="utf-8">
<title>Bayfield Capital Works – Business Card</title>
<link rel="stylesheet" href="https://fonts.googleapis.com/css2?family=Montserrat:wght@400;500;700&display=swap">
<style>
  :root {
    --navy: #1c386b;
    --lime: #8cc63f;
    --white: #ffffff;
    --ink: #1f1f1f;
    --backdrop: #e9eaec;
  }
  * { box-sizing: border-box; margin: 0; padding: 0; }
  html, body { width: 1093px; height: 1200px; overflow: hidden; }
  body {
    background: var(--backdrop);
    font-family: "Montserrat", Arial, sans-serif;
    position: relative;
  }
  .card {
    position: absolute;
    left: 264px;
    width: 582px;
    height: 364px;
    border-radius: 20px;
    overflow: hidden;
  }
  .card--front { top: 225px; background: var(--white); }
  .card--back  { top: 615px; background: var(--lime); }

  /* front */
  .brand-block {
    position: absolute;
    left: 50px; top: 85px;
    width: 184px; height: 152px;
    display: flex; align-items: center; justify-content: center; gap: 10px;
  }
  .brand-block__square {
    width: 18px; height: 18px; background: var(--navy);
  }
  .brand-block__name {
    font-weight: 700; font-size: 24px; color: var(--navy); letter-spacing: 1px;
  }
  .divider {
    position: absolute;
    left: 258px; top: 74px;
    width: 1.5px; height: 163px;
    background: var(--navy);
  }
  .person {
    position: absolute;
    left: 272px; top: 72px;
  }
  .person__name {
    font-weight: 700; font-size: 22px; color: var(--navy); line-height: 1.2;
  }
  .person__title {
    font-weight: 400; font-size: 13px; color: var(--ink); margin-top: 1px;
  }
  .contacts {
    position: absolute;
    left: 274px; top: 160px;
    list-style: none;
  }
  .contacts li {
    display: flex; align-items: center; gap: 9px;
    font-size: 12.6px; color: var(--ink);
    height: 19.5px;
  }
  .contacts li:nth-child(2) { margin-top: 5px; }
  .contacts svg { width: 12px; height: 12px; fill: var(--navy); flex: none; }

  .company {
    position: absolute;
    left: 0; right: 0;
    text-align: center;
  }
  .company__name {
    font-weight: 700; font-size: 23px; color: var(--navy);
    letter-spacing: 0.3px; line-height: 1;
  }
  .company__tagline {
    font-weight: 700; font-size: 11.4px; letter-spacing: 1.6px;
    margin-top: 5px; line-height: 1;
  }
  .card--front .company { top: 303px; }
  .card--front .company__tagline { color: var(--lime); }

  /* back */
  .back-brand {
    position: absolute;
    left: 0; right: 0; top: 90px; height: 136px;
    display: flex; align-items: center; justify-content: center; gap: 12px;
  }
  .back-brand__square { width: 22px; height: 22px; background: var(--navy); }
  .back-brand__name { font-weight: 700; font-size: 30px; color: var(--navy); letter-spacing: 1px; }
  .card--back .company { top: 240px; }
  .card--back .company__name { font-size: 26px; }
  .card--back .company__tagline { color: var(--white); font-size: 12.2px; letter-spacing: 1.6px; }
</style>
</head>
<body>

<section class="card card--front" aria-label="Card front">
  <div class="brand-block">
    <span class="brand-block__square"></span>
    <span class="brand-block__name">BAYFIELD</span>
  </div>
  <div class="divider"></div>
  <div class="person">
    <p class="person__name">Glen R. Harlow</p>
    <p class="person__title">Small Business Advisor</p>
  </div>
  <ul class="contacts">
    <li>
      <svg viewBox="0 0 12 12" aria-hidden="true"><path d="M1 4.5C1 3 3 2 6 2s5 1 5 2.5v1H8.5V4.2H3.5v1.3H1z M2.5 6h7l1 4h-9z"/></svg>
      (555) 806-2147
    </li>
    <li>
      <svg viewBox="0 0 12 12" aria-hidden="true"><path d="M2.5 1l2 2.3-1 1.4c.7 1.5 1.8 2.6 3.3 3.3l1.4-1 2.3 2-1.2 1.6C5.5 10.4 1.6 6.5 1 2.2z"/></svg>
      (555) 274-3918
    </li>
    <li>
      <svg viewBox="0 0 12 12" aria-hidden="true"><path d="M1 2.5h10v1L6 6.5 1 3.5z M1 4.8l5 3 5-3v4.7H1z"/></svg>
      g.harlow@bayfieldcapitalworks.example
    </li>
    <li>
      <svg viewBox="0 0 12 12" aria-hidden="true"><circle cx="6" cy="6" r="5"/><path d="M3 4h2.5l.5 2-1.5 1v2L3 7.5z M7 2.5l2 1-.5 2h-2z" fill="#ffffff"/></svg>
      www.bayfieldcapitalworks.example
    </li>
  </ul>
  <div class="company">
    <p class="company__name">BAYFIELD CAPITAL WORKS, INC</p>
    <p class="company__tagline">SMART GUIDANCE TO BUY OR SELL YOUR NEXT VENTURE</p>
  </div>
</section>

<section class="card card--back" aria-label="Card back">
  <div class="back-brand">
    <span class="back-brand__square"></span>
    <span class="back-brand__name">BAYFIELD</span>
  </div>
  <div class="company">
    <p class="company__name">BAYFIELD CAPITAL WORKS, INC</p>
    <p class="company__tagline">SMART GUIDANCE TO BUY OR SELL YOUR NEXT VENTURE</p>
  </div>
</section>

</body>
</html>
```